Creative, fresh business card design for Ripplecraft Facades

We need a fresh, creative business card design for Ripplecraft Facades. We are the manufacturer of Ripplecraft Facades in Australia. Wall panels are 2400 x 1200mm panels made from MDF and feature 3D patterns on the face of the panel. The colours to be used are green, silver/grey and white RGB
Red 187
Green 207
Blue 65.

An idea is to possibly use a watermark of one of our designs as a background (like on the "Grids" design on the left hand side of page 2 of our brochure).

Target Market(s)

Interior designers, architects, builders and home renovators

Industry/Entity Type

Business

Contact Information for Business Card

Details to go on the card are:
Our logo (attached),
Slogan: "Decorative panels for interiors and exteriors",
Contact name,
Position,
Mobile phone number,
Business address,
Business phone,
Business fax,
Website and
Email address.

I have attached a few images of our panels and our brochure for reference.

The colours of the business card should feature our logo colours which are: RGB
Red 187
Green 207
Blue 65

Requirements
Must have
• Very modern fonts and design. Some of the designs shown especially the "Prisms" design which is a popular design.
Nice to have
• Creative but simple design. Very contemporary.
Should not have
• Anything ornate or old fashioned.

```html
<!DOCTYPE html>
<html lang="en">
<head>
<meta charset="utf-8">
<title>Ripplecraft Facades — Business Card</title>
<link href="https://fonts.googleapis.com/css2?family=Questrial&display=swap" rel="stylesheet">
<style>
  :root {
    --stage: #2b2b2b;
    --card-black: #050505;
    --card-front: #121212;
    --ripple-tone: #1a1a1a;
    --lime: #bbcf41;
    --silver: #b9b9b9;
    --silver-dark: #8e8e8e;
    --white: #f2f2f2;
  }
  * { box-sizing: border-box; margin: 0; padding: 0; }
  html, body { width: 1200px; height: 900px; overflow: hidden; }
  body {
    background: var(--stage);
    font-family: "Questrial", "Helvetica Neue", Arial, sans-serif;
    position: relative;
  }
  .card {
    position: absolute;
    left: 300px;
    width: 600px;
    height: 343px;
    border-radius: 3px;
    box-shadow: 0 10px 28px rgba(0,0,0,.5);
    overflow: hidden;
  }
  .card--back { top: 70px; background: var(--card-black); }
  .card--front { top: 470px; background: var(--card-front); }

  /* back */
  .back-brand {
    position: absolute; left: 0; right: 0; top: 128px;
    display: flex; flex-direction: column; align-items: center;
  }
  .brand-row { display: flex; align-items: center; gap: 12px; }
  .brand-mark { width: 22px; height: 22px; background: var(--silver); }
  .brand-name { color: var(--silver); font-size: 30px; letter-spacing: .5px; }
  .brand-slogan {
    margin-top: 10px; color: var(--silver-dark); font-size: 13px;
    letter-spacing: 3px; text-align: center; line-height: 1.35;
  }

  /* front */
  .ripple-texture {
    position: absolute; inset: 0;
    background: radial-gradient(circle at 30% 40%, var(--ripple-tone), var(--card-front) 70%);
  }
  .front-brand { position: absolute; left: 36px; top: 112px; width: 270px; }
  .front-brand .brand-mark { background: var(--lime); width: 20px; height: 20px; }
  .front-brand .brand-name { color: var(--lime); font-size: 24px; }
  .front-brand .brand-band {
    margin-top: 10px; height: 20px; background: var(--silver);
  }
  .front-brand .brand-slogan {
    text-align: left; color: var(--silver-dark); font-size: 11px; letter-spacing: 2.6px;
  }
  .divider {
    position: absolute; left: 322px; top: 72px; width: 2px; height: 148px;
    background: var(--lime);
  }
  .contact { position: absolute; left: 340px; top: 66px; }
  .contact-name { color: var(--lime); font-size: 22px; letter-spacing: .5px; }
  .contact-role { color: var(--silver); font-size: 12px; letter-spacing: 1px; margin-top: 2px; }
  .contact-list { list-style: none; margin-top: 14px; }
  .contact-list li {
    display: flex; align-items: center; gap: 10px;
    color: var(--silver); font-size: 13px; letter-spacing: 1.4px; height: 22px;
  }
  .contact-list svg { width: 13px; height: 13px; fill: var(--lime); stroke: var(--lime); }
  .address {
    position: absolute; left: 0; right: 0; bottom: 28px; text-align: center;
    color: var(--silver-dark); font-size: 13px; letter-spacing: 1.4px;
  }
</style>
</head>
<body>

<section class="card card--back">
  <div class="back-brand">
    <div class="brand-row">
      <span class="brand-mark"></span>
      <span class="brand-name">Ripplecraft Facades</span>
    </div>
    <p class="brand-slogan">decorative panels for<br>interiors &amp; landscapes</p>
  </div>
</section>

<section class="card card--front">
  <div class="ripple-texture" role="img" aria-label="Faint embossed ripple panel pattern across the card"></div>

  <div class="front-brand">
    <div class="brand-row">
      <span class="brand-mark"></span>
      <span class="brand-name">Ripplecraft Facades</span>
    </div>
    <div class="brand-band"></div>
    <p class="brand-slogan">decorative panels for<br>interiors &amp; landscapes</p>
  </div>

  <div class="divider"></div>

  <div class="contact">
    <h1 class="contact-name">Jonas Albrecht</h1>
    <p class="contact-role">President</p>
    <ul class="contact-list">
      <li><svg viewBox="0 0 12 12"><rect x="3" y="0.5" width="6" height="11" rx="1" fill="none" stroke-width="1.2"/></svg>402.555.0148</li>
      <li><svg viewBox="0 0 12 12"><path d="M2 1l2.5 0 1 3-1.5 1c.8 1.6 1.9 2.7 3.5 3.5l1-1.5 3 1V11c-5 0-9.5-4.5-9.5-10z" stroke="none"/></svg>402.555.0193</li>
      <li><svg viewBox="0 0 12 12" stroke="none"><rect x="3" y="1" width="6" height="3"/><rect x="1" y="4.5" width="10" height="5" rx="1"/><rect x="3" y="8" width="6" height="3"/></svg>402.555.0176</li>
      <li><svg viewBox="0 0 12 12" stroke="none"><path d="M1 2.5h10v7H1z M1 2.5l5 4 5-4"/></svg>jonas@ripplecraft.example</li>
      <li><svg viewBox="0 0 12 12" fill="none" stroke-width="1"><circle cx="6" cy="6" r="5"/><ellipse cx="6" cy="6" rx="2.2" ry="5"/><path d="M1 6h10"/></svg>www.ripplecraft.example</li>
    </ul>
  </div>

  <p class="address">412 Harbour Lane, Marlow Bay, NSW 2150</p>
</section>

</body>
</html>
```